New website for actress www.miriam-halvorsen.de

My website is a little old and needs a new look.
I am a german actress who is in the TV and Theaterbusiness.
my twitter account is called MirHalvorsen
this design will be set up as wordpress site and needs to be optimized for mobile,
so please provide mobile screen views too.
the content will not change much from the excisting site but I would like to have a news section with Videos and press Releases
I would also like my twitter feed to be displayed on my landing page.
I am looking forward to your ideas
best regards
miriam

Target Market(s)

press and fans

Industry/Entity Type

Tv

Font styles to use
Serif
Sans Serif

Colors

Designer to choose colors to be used in the design.

Requirements
Must have
• see above

```html
<!DOCTYPE html>
<html lang="de">
<head>
<meta charset="utf-8">
<title>Miriam Halvorsen – Schauspielerin</title>
<link href="https://fonts.googleapis.com/css2?family=Alegreya+Sans:wght@400;500&display=swap" rel="stylesheet">
<style>
:root{
  --ink:#333;
  --dark:#2e2e2e;
  --sky:#1a9fe0;
  --tw:#11a3df;
  --footer:#2f3033;
  --footer-deep:#262729;
  --link:#e6e6e6;
  --icon:#8b8c8f;
  --active:#0a6ea8;
  --pink:#ff0a5a;--orange:#ff4e12;--red:#ff2525;--teal:#0cc2c9;
  --lilac:#d48fd8;--purple:#6a1fb0;--blue:#0a5ccc;--rose:#ff62b0;
}
*{margin:0;padding:0;box-sizing:border-box}
html,body{width:909px;height:1200px;overflow:hidden}
body{position:relative;background:#f7f8fa;font-family:"Alegreya Sans",sans-serif;color:var(--ink)}
.abs{position:absolute}

.hero{left:0;top:0;width:909px;height:484px;background:radial-gradient(ellipse at 35% 35%,#ffffff 0%,#eef7fc 30%,#c6e6f6 65%,#a4d5ef 100%)}
.email{left:81px;top:3px;font-size:11px;color:#444}
.social{left:637px;top:0;display:flex}
.social span{width:19.7px;height:19px;display:flex;align-items:center;justify-content:center}
.social span::after{content:"";width:6px;height:6px;border-radius:50%;background:#fff}
.brand{left:82px;top:38px;font-size:27px;color:#333;font-weight:400}
.welcome{left:75px;top:110px;width:275px;height:33px;background:var(--sky);color:#fff;font-size:17px;line-height:33px;text-align:center}
.video{left:75px;top:154px;width:320px;height:218px;background:#9fc0cf;padding:5px}
.video .screen{width:100%;height:100%;background:#000;padding:17px 0;position:relative}
.video .still{width:100%;height:100%;background:linear-gradient(90deg,#8b8a80 0%,#c9a36a 35%,#d8b47a 55%,#5c4a3a 80%,#8e8a80 100%)}
.play{position:absolute;width:37px;height:26px;background:#1b1b1b;border-radius:6px;display:flex;align-items:center;justify-content:center}
.caption{left:90px;top:377px;font-size:10px;color:#333}
.dots{left:420px;top:410px;display:flex;gap:5px}
.dots i{width:9px;height:9px;border-radius:50%;background:#8a8d90;display:block}
.dots i.on{background:var(--active)}
.portrait{left:596px;top:92px;width:192px;height:336px;background:linear-gradient(180deg,rgba(240,225,200,0) 0%,#f0dcc0 12%,#e6a08f 35%,#e8858d 50%,#ef6a3a 70%,#e2481c 100%)}

.nav{left:0;top:428px;width:909px;height:56px}
.nav a{position:absolute;top:0;height:56px;font-size:10.5px;font-weight:500;text-transform:uppercase;color:#2b2b2b;text-decoration:none;text-align:center;padding-top:34px}

.intro{left:118px;top:505px;width:673px;font-size:13px;line-height:16.5px;text-align:center;color:#333}
.btn{height:25px;background:var(--dark);color:#fff;font-size:12.5px;line-height:25px;text-align:center}
.rule{left:94px;width:720px;height:5px;border-top:1px dotted #999;border-bottom:1px dotted #999}
.worked{left:0;top:640px;width:909px;text-align:center;font-size:15px;font-weight:400;color:#333}
.arrow{top:646px;width:18px;height:18px;display:flex;align-items:center;justify-content:center}
.thumb{top:673px;height:151px}

.twitter{left:0;top:878px;width:909px;height:76px;background:var(--tw)}
.twitter p{position:absolute;left:150px;top:29px;font-size:12.5px;color:#fff}
.follow{position:absolute;left:745px;top:30px;width:69px;height:19px;background:var(--active);color:#fff;font-size:8px;line-height:19px;text-align:center}

.footer{left:0;top:954px;width:909px;height:208px;background:var(--footer);color:#fff}
.col{position:absolute;top:28px}
.col h3{font-size:14px;font-weight:400;margin-bottom:11px}
.col li{list-style:none;font-size:10px;line-height:16px;color:var(--link)}
.contact p{font-size:9.5px;line-height:16px;color:var(--link)}
.icons{display:flex;gap:9px;margin-top:11px}
.icons i{width:9px;height:9px;border:1.5px solid var(--icon);border-radius:2px;display:block}
.bottom{left:0;top:1162px;width:909px;height:38px;background:var(--footer-deep);color:var(--link);font-size:9.5px}
.bottom .copy{position:absolute;left:95px;top:13px}
.bottom .legal{position:absolute;right:94px;top:13px;display:flex;gap:9px}
</style>
</head>
<body>
<header class="abs hero">
  <div class="abs email">me@miriam-halvorsen.de</div>
  <div class="abs social" aria-label="Soziale Netzwerke">
    <span style="background:#3b5998"></span><span style="background:#29b6f2"></span><span style="background:#e22d1f"></span><span style="background:#ea6fa0"></span><span style="background:#cc1a2a"></span><span style="background:#1e7a3a"></span><span style="background:#f39014"></span><span style="background:#1aa8d6"></span><span style="background:#5a21a8"></span><span style="background:#3c3c3c"></span>
  </div>
  <h1 class="abs brand">Miriam Halvorsen</h1>
  <div class="abs welcome">Hallo Und Herzlich Willkommen</div>
  <div class="abs video">
    <div class="screen">
      <div class="still" role="img" aria-label="Video-Standbild: Interview mit Miriam Halvorsen"></div>
      <div class="play" style="left:137px;top:98px"><svg width="12" height="13"><path d="M1 0 L12 6.5 L1 13Z" fill="#fff"/></svg></div>
    </div>
  </div>
  <div class="abs caption">Donec sed odio dui. Nulla vitae elit libero, a pharetra augue.</div>
  <div class="abs dots"><i></i><i></i><i class="on"></i><i></i><i></i></div>
  <div class="abs portrait" role="img" aria-label="Foto: die Schauspielerin stehend in gestreiftem Oberteil und orangem Rock"></div>
  <nav class="abs nav">
    <a style="left:76px;width:86px;background:var(--pink)">Biographie</a>
    <a style="left:165px;width:87px;background:var(--orange)">Interview</a>
    <a style="left:255px;width:107px;background:var(--red)">Theatrefotos</a>
    <a style="left:365px;width:102px;background:var(--teal)">Privatfotos</a>
    <a style="left:470px;width:95px;background:var(--lilac)">Eroticfotos</a>
    <a style="left:568px;width:104px;background:var(--purple)">Autogramme</a>
    <a style="left:676px;width:77px;background:var(--blue)">Charity</a>
    <a style="left:757px;width:77px;background:var(--rose)">Kontakt</a>
  </nav>
</header>

<main>
  <p class="abs intro">in meiner welt. Hier findet Ihr Augenblikke meiner Arbeit, Einblicke in meine ganz privaten Ansichten und Ausblicke auf meine aktullen Projekte fur Fernsehen, Theater, Film and mehr. Einfach uf die gewunschte Rubrik klicken und schon zeige ich, wasda-hinterteckt.</p>
  <div class="abs btn" style="left:343px;top:571px;width:104px">See Gallery</div>
  <div class="abs btn" style="left:470px;top:571px;width:104px">See Portfolio</div>
  <div class="abs rule" style="top:620px"></div>
  <h2 class="abs worked">Something I've worked on</h2>
  <div class="abs arrow" style="left:768px;background:#8f9295"><svg width="6" height="9"><path d="M5 1 L1.5 4.5 L5 8" stroke="#fff" stroke-width="1.6" fill="none"/></svg></div>
  <div class="abs arrow" style="left:788px;background:var(--active)"><svg width="6" height="9"><path d="M1 1 L4.5 4.5 L1 8" stroke="#fff" stroke-width="1.6" fill="none"/></svg></div>
  <div class="abs thumb" style="left:95px;width:227px;background:linear-gradient(180deg,#6b7a5a 0%,#b9b7ae 45%,#d8475a 75%,#d01c22 100%)" role="img" aria-label="Video: Auftritt auf dem roten Teppich"></div>
  <div class="abs play" style="left:184px;top:735px"><svg width="12" height="13"><path d="M1 0 L12 6.5 L1 13Z" fill="#fff"/></svg></div>
  <div class="abs thumb" style="left:341px;width:227px;background:linear-gradient(90deg,#bcd8f0 0%,#cbb089 35%,#c6a77e 60%,#bcd8f0 100%)" role="img" aria-label="Foto: Porträt vor hellblauem Hintergrund"></div>
  <div class="abs thumb" style="left:588px;width:225px;background:linear-gradient(180deg,#d2c49c 0%,#b89a74 50%,#cfc09a 100%)" role="img" aria-label="Video: Filmplakat in warmen Sandtönen"></div>
  <div class="abs play" style="left:683px;top:735px"><svg width="12" height="13"><path d="M1 0 L12 6.5 L1 13Z" fill="#fff"/></svg></div>
  <div class="abs rule" style="top:848px"></div>
</main>

<section class="abs twitter">
  <svg class="abs" style="left:100px;top:24px" width="28" height="28"><circle cx="14" cy="14" r="11" fill="#fff"/></svg>
  <p>There are many variations of passages of Lorem Ipsum available, but the majority have suffered alteration.</p>
  <div class="follow">Follow Me</div>
</section>

<footer class="abs footer">
  <div class="col" style="left:95px"><h3>Quick Links</h3><ul><li>Home</li><li>About</li><li>Biography</li><li>Interview</li><li>Theater</li><li>Private</li><li>Erotic</li><li>Charity</li><li>Contact</li></ul></div>
  <div class="col" style="left:216px"><h3>Support Links</h3><ul><li>Home</li><li>About</li><li>Biography</li><li>Interview</li><li>Theater</li><li>Private</li><li>Erotic</li><li>Charity</li><li>Contact</li></ul></div>
  <div class="col" style="left:345px"><h3>Latest Blog Posts</h3><ul><li>Home</li><li>About</li><li>Biography</li><li>Interview</li><li>Theater</li><li>Private</li><li>Erotic</li><li>Charity</li><li>Contact</li></ul></div>
  <div class="col" style="left:485px"><h3>Support Links</h3><ul><li>Home</li><li>About</li><li>Biography</li><li>Interview</li><li>Theater</li><li>Private</li><li>Erotic</li><li>Charity</li><li>Contact</li></ul></div>
  <div class="col contact" style="left:603px"><h3>Contact Us</h3>
    <p>Studio 4, Lindenhof Atelier, Kastanienweg, Hamburg.</p>
    <p>Tel : +49 40 555 0182 , Fax : +49 40 555 0183</p>
    <p>info@studiohalvorsen.com</p>
    <div class="icons" aria-label="Soziale Netzwerke"><i></i><i></i><i></i><i></i><i></i><i></i><i></i><i></i><i></i><i></i><i></i></div>
  </div>
</footer>
<div class="abs bottom">
  <div class="copy">Copyright © 2002-2014 Miriam Halvorsen. All rights</div>
  <div class="legal"><span>Privacy Policy</span><span>Legal</span><span>Disclaimer</span></div>
</div>
</body>
</html>
```